Fitness Equipment & Service

I want to make the card eye catching and fun. We are called Corvane Motion Limited and we are based in Wales. We sell, install and service all types of fitness equipment from Skipping ropes, right through the Dumbbells, Kettle bells and Barbells through to state of the art Treadmills, Running Machines and Strength Equipment. We also design and install changing room furniture and lockers.

TYPOGRAPHY
We would like to use Futrura. Futura has an appearance of efficiency and forwardness. The typeface is derived
from simple geometric forms (near-perfect circles, triangles and squares) and is based on strokes of
near-even weight, which are low in contrast. This is most visible in the almost perfectly round stroke of
the o, which is nonetheless slightly ovoid.
The lowercase has tall ascenders, which rise above the cap line. The uppercase
characters present proportions similar to those of classical Roman capitals.

TYPOGRAPHIC CONSIDERATIONS
No Strike though
No Horizontal Scaling
No Drop Shadows
No Effects
Never use less than 120% Leading

OUR CORPORATE COLOURS
BRAND GUIDELINES
We were thinking that our primary colour palette consists of the Acid Green (Pantone 382) and Process Black.

We work closely with tquarly Ltd and would like to include their name on the card somewhere. I have attached images of the other brands that we work with as an idea or the small icons I have included that illustrate what we do?. I have very kindly been given permission to use any of the images off the files that I have included below, so I hope these help. I will include these below. I would be open to suggestions if it made the card more striking Can you do it?
Updates

Hi All, Just wanted to add a few thoughts but you are the guys with the creative visions (thats why are here) We are based in Wales, UK and we would be open to lots of different ideas on a theme but must be eye catching, Bold and FUN. If you can or think that the Welsh or any dragon could be put in there then go for it (its not a must have) We have also added some ideas for colour but again its over to you!! GO FOR IT ! Thanks and look forward to your visions! Owen

Hi All, Just thought I would sen through the contact details that need to be on the card. (if you want to play around with icons instead of the wording twitter, Facebook, go for it): Corvane Motion Limited Owen Pritchard Managing Director Mob: +44 (0)7582 913 406 e-mail: sales@corvanemotion.co.uk Web: Corvanemotion.co.uk twitter: @motionLetterbin Facebook: Corvane Motion Limited

```html
<!DOCTYPE html>
<html lang="en">
<head>
<meta charset="utf-8">
<title>Corvane Motion Limited – Business Card</title>
<link rel="stylesheet" href="https://fonts.googleapis.com/css2?family=Jost:wght@400;600&display=swap">
<style>
  :root {
    --stage: #e9e7e3;
    --card-white: #ffffff;
    --brand-blue: #1f5fa8;
    --brand-blue-deep: #163f7a;
    --brand-navy: #2b3370;
    --tile-sky: #35b8e6;
    --tile-mid: #2a78c0;
    --tile-dark: #1a4f8c;
    --tile-grey: #7f93a8;
    --tile-pale: #a9b9c8;
    --accent-gold: #c9a43a;
    --ink: #3a3a3a;
  }
  * { margin: 0; padding: 0; box-sizing: border-box; }
  html, body {
    width: 1200px; height: 892px; overflow: hidden;
    background: var(--stage);
    font-family: "Jost", "Futura", sans-serif;
  }
  .canvas { position: relative; width: 1200px; height: 892px; }

  .card {
    position: absolute; width: 600px; height: 343px;
    border-radius: 4px; overflow: hidden;
    box-shadow: 0 6px 18px rgba(0,0,0,.18);
  }

  /* Front */
  .card-front { left: 300px; top: 60px; background: var(--card-white); }
  .front-band { position: absolute; left: 0; bottom: 0; width: 600px; height: 343px; }
  .brand {
    position: absolute; left: 34px; top: 34px;
    display: flex; align-items: center; gap: 14px;
  }
  .brand-disc {
    width: 64px; height: 64px; border-radius: 50%;
    background: var(--brand-blue-deep);
  }
  .brand-name {
    font-weight: 600; font-size: 22px; line-height: 1.2;
    color: var(--brand-navy); width: 150px;
  }
  .holder {
    position: absolute; right: 34px; top: 34px; text-align: right;
  }
  .holder-name {
    font-weight: 600; font-size: 30px; line-height: 1.2; color: var(--brand-blue);
  }
  .holder-role { font-size: 17px; line-height: 1.3; color: var(--ink); }
  .contacts {
    position: absolute; right: 34px; top: 130px;
    list-style: none; text-align: right;
  }
  .contacts li {
    display: flex; justify-content: flex-end; align-items: center; gap: 10px;
    font-size: 17px; line-height: 1.35; color: var(--ink);
  }
  .contact-icon {
    width: 15px; height: 15px; border-radius: 2px;
    background: var(--brand-blue); display: inline-flex;
    align-items: center; justify-content: center;
  }

  /* Back */
  .card-back {
    left: 300px; top: 470px;
    background: linear-gradient(135deg, var(--tile-mid), var(--brand-blue-deep));
  }
  .tile-grid {
    position: absolute; inset: 0;
    display: grid; grid-template-columns: repeat(5, 1fr); grid-template-rows: repeat(3, 1fr);
  }
  .tile { opacity: .95; }
  .tile--sky { background: var(--tile-sky); }
  .tile--mid { background: var(--tile-mid); }
  .tile--dark { background: var(--tile-dark); }
  .tile--grey { background: var(--tile-grey); }
  .tile--pale { background: var(--tile-pale); }
  .tile--clear { background: transparent; }
  .back-name {
    position: absolute; left: 175px; top: 112px;
    font-weight: 600; font-size: 46px; line-height: 1.2; color: var(--card-white);
    width: 400px;
  }
</style>
</head>
<body>
<main class="canvas">

  <section class="card card-front" aria-label="Business card front">
    <svg class="front-band" viewBox="0 0 600 343" aria-hidden="true">
      <path d="M0 215 C150 225 260 262 380 290 C470 310 540 325 600 330 L600 343 L0 343 Z" fill="var(--accent-gold)"/>
      <path d="M0 224 C150 234 260 270 380 298 C470 317 540 332 600 338 L600 343 L0 343 Z" fill="var(--brand-blue)"/>
      <path d="M0 224 C150 234 260 270 380 298 L380 343 L0 343 Z" fill="var(--tile-mid)" opacity=".5"/>
    </svg>

    <div class="brand">
      <span class="brand-disc"></span>
      <span class="brand-name">Corvane Motion Limited</span>
    </div>

    <div class="holder">
      <p class="holder-name">Owen Pritchard</p>
      <p class="holder-role">Managing Director</p>
    </div>

    <ul class="contacts">
      <li>+44 (0)7582 913 406
        <span class="contact-icon"><svg width="9" height="9" viewBox="0 0 10 10"><path d="M2 1 L4 1 L5 3 L4 4 C4.5 5.5 5 6 6 6 L7 5 L9 6 L9 8 C5 9 1 5 2 1 Z" fill="#fff"/></svg></span></li>
      <li>sales@corvanemotion.co.uk
        <span class="contact-icon"><svg width="10" height="8" viewBox="0 0 10 8"><rect x=".5" y=".5" width="9" height="7" fill="none" stroke="#fff"/><path d="M.5 .5 L5 4.5 L9.5 .5" fill="none" stroke="#fff"/></svg></span></li>
      <li>Corvanemotion.co.uk
        <span class="contact-icon"><svg width="10" height="10" viewBox="0 0 10 10"><circle cx="5" cy="5" r="4" fill="none" stroke="#fff"/><path d="M1 5 H9 M5 1 V9" stroke="#fff"/></svg></span></li>
      <li>@motionLetterbin <span class="contact-icon"></span></li>
      <li>Corvane Motion Limited <span class="contact-icon"></span></li>
    </ul>
  </section>

  <section class="card card-back" aria-label="Business card back">
    <div class="tile-grid">
      <div class="tile tile--mid" role="img" aria-label="Treadmill icon"></div>
      <div class="tile tile--sky" role="img" aria-label="Exercise bike icon"></div>
      <div class="tile tile--clear"></div>
      <div class="tile tile--clear"></div>
      <div class="tile tile--clear"></div>
      <div class="tile tile--clear" role="img" aria-label="Faint dumbbell photograph"></div>
      <div class="tile tile--grey" role="img" aria-label="Kettlebell icon"></div>
      <div class="tile tile--clear"></div>
      <div class="tile tile--clear"></div>
      <div class="tile tile--dark"></div>
      <div class="tile tile--dark" role="img" aria-label="Skipping rope icon"></div>
      <div class="tile tile--mid" role="img" aria-label="Nutrition drink and apple icon"></div>
      <div class="tile tile--pale" role="img" aria-label="Bathroom scale icon"></div>
      <div class="tile tile--clear"></div>
      <div class="tile tile--mid" role="img" aria-label="Boxing gloves icon"></div>
    </div>
    <p class="back-name">Corvane Motion Limited</p>
  </section>

</main>
</body>
</html>
```